Redesign Website - Current one too plain

The description is in the uploaded file. Please let me know if you need any more information. I'd prefer it if someone could implement the design to a WordPress site but the best design will win, regardless.
I would like the forms to look nice as well
UPDATE:
I don't think we can use the images that I provided, I think they make the site look a bit 'cheap' and I really don't know how to replace them. One thought I have had is to make the "Simple, Unique, Effective" a second feature on the right side of the page with the search on the left
Target Market(s)
Small companies, private sellers of cars and people who rent their caravan/holiday home out
Industry/Entity Type
Advertising
Number of Pages Required
3 page
Colors
Designer to choose colors to be used in the design.
Look and feel
Each slider illustrates characteristics of the customer's brand and the style your logo design should communicate.

```html
<!DOCTYPE html>
<html lang="en">
<head>
<meta charset="utf-8">
<title>CODRA – Find a business by its code</title>
<link rel="stylesheet" href="https://fonts.googleapis.com/css2?family=Outfit:wght@300;400;500;600;700&family=Archivo+Black&display=swap">
<style>
  :root {
    --lime: #e2fb14;
    --lime-text: #a6d21c;
    --ink: #141414;
    --muted: #555;
    --pill: #ececec;
    --panel-a: #f3f4f6;
    --panel-b: #e4e6ea;
    --white: #ffffff;
    --chevron: #444;
  }
  * { box-sizing: border-box; margin: 0; padding: 0; }
  html, body { width: 1200px; height: 1068px; overflow: hidden; background: var(--white); }
  body { position: relative; font-family: "Outfit", sans-serif; color: var(--ink); }

  .site-header { position: absolute; left: 0; top: 0; width: 1200px; height: 100px; }
  .brand { position: absolute; left: 161px; top: 36px; display: flex; align-items: center; gap: 8px;
    font-size: 24px; font-weight: 400; letter-spacing: 4px; color: var(--lime-text); }
  .brand-dot { width: 20px; height: 20px; border-radius: 50%; background: var(--lime-text); }
  .main-nav { position: absolute; left: 471px; top: 42px; display: flex; gap: 20px; font-size: 13.5px; }
  .main-nav a { color: var(--ink); text-decoration: none; }
  .main-nav a.is-active { color: var(--lime-text); font-weight: 500; }
  .login-btn { position: absolute; left: 909px; top: 30px; width: 130px; height: 40px; border-radius: 20px;
    background: var(--lime); font-size: 14px; display: flex; align-items: center; justify-content: center; }

  .hero { position: absolute; left: 21px; top: 104px; width: 1159px; height: 605px; border-radius: 22px;
    overflow: hidden; background: linear-gradient(100deg, var(--panel-b) 0%, var(--panel-a) 12%, #fafafa 50%, #f6f6fa 100%); }
  .hero-illustration { position: absolute; left: 470px; top: 0; width: 689px; height: 605px;
    background: linear-gradient(160deg, #f8f8fb 0%, #eef0fa 35%, #dfe3f6 50%, #6fe07a 68%, #21c6b6 82%, #3e7be6 100%);
    clip-path: polygon(100% 0, 100% 100%, 0 100%, 0 95%, 60% 45%, 75% 0); }
  .search-card { position: absolute; left: 53px; top: 71px; width: 464px; height: 471px; border-radius: 45px;
    background: linear-gradient(180deg, #cfe6f2 0%, #eef4f7 40%, #fafafa 75%, #f7f7f7 100%); }
  .code-picker { position: absolute; left: 0; top: 0; width: 464px; height: 280px; }
  .chevron { position: absolute; width: 22px; height: 12px; }
  .chevron-up { top: 66px; }
  .chevron-down { top: 250px; }
  .code-char { position: absolute; top: 85px; font-family: "Archivo Black", sans-serif; font-size: 172px;
    line-height: 1; color: var(--ink); transform: translateX(-50%) scaleX(1.25); }
  .category-list { position: absolute; left: 33px; top: 291px; display: flex; gap: 6px; }
  .category-pill { width: 129px; height: 45px; border-radius: 23px; background: var(--pill);
    display: flex; align-items: center; justify-content: center; font-size: 14.5px; }
  .search-btn { position: absolute; left: 152px; top: 383px; width: 160px; height: 42px; border-radius: 21px;
    background: var(--lime); display: flex; align-items: center; justify-content: space-between; padding: 0 17px 0 28px;
    font-size: 14.5px; font-weight: 500; }
  .advertise-btn { position: absolute; left: 764px; top: 498px; width: 253px; height: 42px; border-radius: 21px;
    background: var(--lime); display: flex; align-items: center; justify-content: space-between; padding: 0 22px 0 26px;
    font-size: 14.5px; font-weight: 500; }

  .features { position: absolute; left: 21px; top: 725px; width: 1159px; height: 261px; border-radius: 22px;
    background: linear-gradient(100deg, #f6f6f6 0%, #fbfbfb 40%, #f3f3f3 80%, #dcdde0 100%); }
  .features-title { position: absolute; left: 140px; top: 103px; }
  .features-title .kicker { display: block; font-size: 26px; font-weight: 400; line-height: 1; }
  .features-title .headline { display: block; font-size: 41px; font-weight: 600; line-height: 1.15; }
  .feature { position: absolute; top: 54px; width: 190px; }
  .feature-icon { width: 36px; height: 36px; }
  .feature h3 { margin-top: 9px; font-size: 27px; font-weight: 700; line-height: 1.2; }
  .feature p { margin-top: 6px; font-size: 15px; line-height: 17.5px; font-weight: 400; }

  .site-footer { position: absolute; left: 162px; top: 1016px; width: 876px; font-size: 15px; display: flex;
    justify-content: space-between; font-weight: 300; }
  .site-footer strong { font-weight: 700; }
  .site-footer .legal { font-weight: 400; }
</style>
</head>
<body>
<header class="site-header">
  <div class="brand"><span class="brand-dot"></span>CODRA</div>
  <nav class="main-nav">
    <a class="is-active" href="#">Home</a>
    <a href="#">Advertise</a>
    <a href="#">Contact</a>
    <a href="#">Register</a>
  </nav>
  <a class="login-btn">LOGIN</a>
</header>

<section class="hero">
  <div class="hero-illustration" role="img" aria-label="Isometric illustration of cars and trucks driving across elevated bridges over a green landscape with trees and water"></div>

  <div class="search-card">
    <div class="code-picker">
      <svg class="chevron chevron-up" style="left:155px" viewBox="0 0 22 12"><path d="M2 11 11 2l9 9" fill="none" stroke="var(--chevron)" stroke-width="2.4"/></svg>
      <svg class="chevron chevron-up" style="left:312px" viewBox="0 0 22 12"><path d="M2 11 11 2l9 9" fill="none" stroke="var(--chevron)" stroke-width="2.4"/></svg>
      <span class="code-char" style="left:166px">A</span>
      <span class="code-char" style="left:323px">1</span>
      <svg class="chevron chevron-down" style="left:155px" viewBox="0 0 22 12"><path d="M2 1l9 9 9-9" fill="none" stroke="var(--chevron)" stroke-width="2.4"/></svg>
      <svg class="chevron chevron-down" style="left:312px" viewBox="0 0 22 12"><path d="M2 1l9 9 9-9" fill="none" stroke="var(--chevron)" stroke-width="2.4"/></svg>
    </div>
    <div class="category-list">
      <span class="category-pill">Car</span>
      <span class="category-pill">Caravan</span>
      <span class="category-pill">Company</span>
    </div>
    <a class="search-btn">Search
      <svg width="17" height="17" viewBox="0 0 18 18"><circle cx="7.5" cy="7.5" r="6" fill="none" stroke="var(--ink)" stroke-width="1.6"/><path d="M12 12l5 5" stroke="var(--ink)" stroke-width="1.6"/></svg>
    </a>
  </div>

  <a class="advertise-btn">Advertise Your Company
    <svg width="18" height="14" viewBox="0 0 18 14"><path d="M1 7h15M10 1l6 6-6 6" fill="none" stroke="var(--ink)" stroke-width="1.8"/></svg>
  </a>
</section>

<section class="features">
  <h2 class="features-title"><span class="kicker">Our Core</span><span class="headline">Features</span></h2>

  <div class="feature" style="left:422px">
    <svg class="feature-icon" viewBox="0 0 36 36" fill="none" stroke="var(--ink)" stroke-width="1.3">
      <circle cx="17" cy="17" r="15"/><circle cx="17" cy="17" r="10.5"/><circle cx="17" cy="17" r="6"/><circle cx="17" cy="17" r="1.6"/>
      <path d="M17 17l12 12M26 33l3-4 4-1"/>
    </svg>
    <h3>Simple</h3>
    <p>Create&nbsp; your<br>advert &amp; display<br>your code.</p>
  </div>

  <div class="feature" style="left:613px">
    <svg class="feature-icon" viewBox="0 0 36 36" fill="none" stroke="var(--ink)" stroke-width="1.3">
      <path d="M18 2l3 3 4-1 1 4 4 1-1 4 3 3-3 3 1 4-4 1-1 4-4-1-3 3-3-3-4 1-1-4-4-1 1-4-3-3 3-3-1-4 4-1 1-4 4 1z"/>
      <circle cx="18" cy="18" r="9"/>
      <path d="M18 12.5l1.7 3.5 3.8.5-2.8 2.6.7 3.8-3.4-1.8-3.4 1.8.7-3.8-2.8-2.6 3.8-.5z"/>
    </svg>
    <h3>Unique</h3>
    <p>Customers find you<br>by an easy-to-remember<br>code.</p>
  </div>

  <div class="feature" style="left:857px">
    <svg class="feature-icon" viewBox="0 0 36 36" fill="none" stroke="var(--ink)" stroke-width="1.3">
      <path d="M3 22l9-8 6 5 14-15M25 4h7v7"/>
      <path d="M2 34h32M6 34v-6M12 34v-9M18 34v-7M24 34v-10M30 34v-13"/>
    </svg>
    <h3>Effective</h3>
    <p>Customers are directed<br>to you and not a list of<br>your competitors.</p>
  </div>
</section>

<footer class="site-footer">
  <span>© 2023 <strong>CODRA.</strong> All rights reserved.</span>
  <span class="legal">Terms &amp; Conditions&nbsp; |&nbsp; Privacy Policy</span>
</footer>
</body>
</html>
```